Investment company needing business card

We are wanting a business card which looks sharp and easy on the eye. We are thinking of having a business card with the logo embossed on it, to really make it stand out. We will only have a small amount of information of the business card, person's name, position, email address and phone number

Contact Information for Business Card

Danielle Frost
Executive Assistant
+64 21 473 5162
danielf@harwickpartners.co.nz

Requirements
Must have
• Embossed logo
Should not have
• Not to be busy

```html
<!DOCTYPE html>
<html lang="en">
<head>
<meta charset="utf-8">
<title>Harwick Partners – Business Card</title>
<link rel="stylesheet" href="https://fonts.googleapis.com/css2?family=Michroma&family=Open+Sans:wght@400&display=swap">
<style>
  :root {
    --stage: #8a8b8e;
    --card: #2a2a2a;
    --card-deep: #1c1c1c;
    --accent: #27b673;
    --slate: #626366;
    --rule: #8d8d8d;
    --text-light: #d6d6d6;
  }
  * { margin: 0; padding: 0; box-sizing: border-box; }
  html, body { width: 1200px; height: 1044px; overflow: hidden; }
  body { background: var(--stage); position: relative; font-family: "Open Sans", sans-serif; }

  .card {
    position: absolute;
    width: 759px; height: 435px;
    border-radius: 32px 0 0 32px;
    background: radial-gradient(ellipse at 55% 35%, #3a3a3a 0%, var(--card) 50%, var(--card-deep) 100%);
    box-shadow: 0 2px 6px rgba(0,0,0,.35);
    overflow: hidden;
  }
  .card--front { left: 84px; top: 56px; }
  .card--back { left: 376px; top: 542px; }

  .brand-name {
    position: absolute;
    font-family: "Michroma", sans-serif;
    color: var(--accent);
    white-space: nowrap;
    letter-spacing: 0.3px;
  }
  .brand-square { position: absolute; background: var(--slate); }

  .card--front .brand-square { left: 29px; top: 54px; width: 96px; height: 96px; }
  .card--front .brand-name { left: 150px; top: 72px; font-size: 24px; line-height: 40px; }

  .person-name {
    position: absolute; left: 30px; top: 236px;
    font-family: "Michroma", sans-serif; font-size: 19px; color: var(--accent);
  }
  .person-role {
    position: absolute; left: 30px; top: 270px;
    font-family: "Michroma", sans-serif; font-size: 15px; color: var(--text-light);
  }
  .role-rule { position: absolute; left: 301px; right: 0; top: 278px; height: 2px; background: var(--rule); }

  .contact-list {
    position: absolute; right: 34px; top: 322px;
    list-style: none; text-align: right;
  }
  .contact-list li {
    display: flex; justify-content: flex-end; align-items: center; gap: 8px;
    font-size: 17px; color: var(--text-light); height: 31px; white-space: nowrap;
  }
  .contact-list svg { width: 17px; height: 17px; flex: none; }

  .card--back .brand-square { left: 32px; top: 63px; width: 310px; height: 310px; border-radius: 4px; }
  .card--back .brand-name { left: 420px; top: 174px; font-size: 18px; line-height: 40px; }
  .card--back .contact-list { right: 40px; top: 252px; }
</style>
</head>
<body>

<section class="card card--front" role="img" aria-label="Business card front on dark embossed leather texture">
  <div class="brand-square"></div>
  <div class="brand-name">HARWICK PARTNERS</div>

  <div class="person-name">DANIELLE FROST</div>
  <div class="person-role">EXECUTIVE ASSISTANT</div>
  <div class="role-rule"></div>

  <ul class="contact-list">
    <li>
      <svg viewBox="0 0 24 24" fill="none" stroke="var(--accent)" stroke-width="2"><circle cx="12" cy="12" r="10"/><path d="M9 7l2 3-1.5 1.5a7 7 0 0 0 3 3L14 13l3 2-1 2c-4 0-9-5-9-9z" fill="var(--accent)" stroke="none"/></svg>
      +64 21 473 5162
    </li>
    <li>
      <svg viewBox="0 0 24 24" fill="var(--accent)"><path d="M2 9l10-6 10 6v11H2z"/><path d="M2 9l10 7 10-7" fill="none" stroke="#2a2a2a" stroke-width="1.5"/></svg>
      danielf@harwickpartners.co.nz
    </li>
    <li>
      <svg viewBox="0 0 24 24" fill="none" stroke="var(--accent)" stroke-width="1.6"><circle cx="12" cy="12" r="10"/><ellipse cx="12" cy="12" rx="4" ry="10"/><path d="M2 12h20M4 7h16M4 17h16"/></svg>
      www.harwickpartners.com/
    </li>
  </ul>
</section>

<section class="card card--back" role="img" aria-label="Business card back on dark embossed leather texture">
  <div class="brand-square"></div>
  <div class="brand-name">HARWICK PARTNERS</div>
  <ul class="contact-list">
    <li>
      <svg viewBox="0 0 24 24" fill="none" stroke="var(--accent)" stroke-width="1.6"><circle cx="12" cy="12" r="10"/><ellipse cx="12" cy="12" rx="4" ry="10"/><path d="M2 12h20M4 7h16M4 17h16"/></svg>
      www.harwickpartners.com/
    </li>
  </ul>
</section>

</body>
</html>
```